Nanny Share Ecommerce Website for Finding Childcare and Parents who need Childcare BrightPramHub.net

Our company needs an ecommerce website (BrightPramHub.net) for a US subscription based service strictly for nanny sharing that connects families and caregivers. The website would allow families to connect with one another as well as to search for nannies. The service would be searchable for other families by location (by radius or zip code), children demographic (age range/gender/special needs), days of week or times, after school care, school closure days (holidays), etc. The service would also be searchable for nannies based on gender, provider age range, years experience, language, hourly rate, transportation available, certification (CPR first aid), education etc. The search fields would be searchable and sortable and allow to connect with the provider (after paying subscription fee). The service would be similar to tendlyfolk.net in that it would allow for families and caregivers to post photos as well as a short bio of the themselves. There would also be a feedback/star rating mechanism to rate caregivers who have performed work for families (viewable to public). The service would be free for nannies to post their bios and only a subscription based service for families to connect with other families or with caregivers (able to view bio but need service to connect). There will be a short bio on the benefits of nanny sharing (reduced cost, increased flexibility for parents, reduced illness, increased socialization with other children vs. sole nanny), as well as Q&A section with best practices.

Target Market(s)

Families, Nannies

Industry/Entity Type

Childcare

Logo Text

Bright Pram Hub

Coding

Coded - Design and coding required

Number of Pages Required

5+ page

Requirements
Must have
• Searchable (need to be able to search for families as well as nannies), responsive, functional, easy to use, add value to families and nannies. Needs to be able to collect payment for subscription.
Nice to have
• Optimized for mobile, SEO optimized

```html
<!DOCTYPE html>
<html lang="en">
<head>
<meta charset="utf-8">
<title>Bright Pram Hub — Nanny for Families and Caregivers</title>
<link href="https://fonts.googleapis.com/css2?family=Roboto:wght@400;500;700&display=swap" rel="stylesheet">
<style>
:root{
  --teal:#33bdb5;
  --pink:#f42b56;
  --ink:#2f2f2f;
  --text:#555;
  --muted:#777;
  --light:#e6e6e6;
  --white:#fff;
}
*{box-sizing:border-box;margin:0;padding:0}
html,body{width:1200px;height:2975px;overflow:hidden}
body{position:relative;background:var(--white);font-family:'Roboto',Arial,sans-serif;color:var(--ink)}
.abs{position:absolute}
a{color:inherit;text-decoration:none}

/* header */
.site-header{left:0;top:0;width:1200px;height:100px;background:var(--white);z-index:5}
.brand{left:62px;top:12px;width:150px;text-align:center}
.brand-mark{display:block;width:40px;height:40px;border-radius:50%;background:var(--pink);margin:0 auto 10px}
.brand-name{font-size:17px;font-weight:700;color:var(--teal)}
.top-phone{left:848px;top:22px;font-size:15px;font-weight:500;color:var(--ink);display:flex;align-items:center;gap:8px}
.btn-login{left:1006px;top:14px;width:94px;height:34px;border-radius:17px;background:var(--pink);color:#fff;font-size:12px;font-weight:700;display:flex;align-items:center;justify-content:center;gap:6px}
.main-nav{right:98px;top:70px;display:flex;gap:37px;font-size:12.5px;font-weight:500;text-transform:uppercase}

/* hero */
.hero{left:0;top:100px;width:1200px;height:880px;background:var(--teal);overflow:hidden}
.hero-bg{left:0;top:0;width:1200px;height:560px;background:linear-gradient(90deg,#f4f4f6 0%,#eeeef0 35%,#e7e4e2 100%)}
.hero-photo{left:430px;top:0;width:770px;height:560px;background:radial-gradient(ellipse at 35% 45%,#d8c1b3 0%,#c9b2a6 28%,#8fc9c2 62%,#b8dcd6 100%)}
.hero-wave{left:0;top:460px}
.hero-title{left:100px;top:177px;font-size:37px;line-height:48px;font-weight:700;color:#333;text-transform:uppercase}
.hero-sub{left:100px;top:290px;font-size:22px;font-weight:500;color:#333}
.btn{height:38px;border-radius:19px;color:#fff;font-size:12px;font-weight:500;display:flex;align-items:center;justify-content:center;text-transform:uppercase}
.btn-find{left:100px;top:343px;width:125px;background:var(--pink)}
.btn-search{left:240px;top:343px;width:175px;background:var(--teal)}

.benefit{top:640px;width:240px;text-align:center;color:#fff}
.benefit-icon{width:70px;height:70px;border-radius:50%;background:#fff;margin:0 auto 30px;display:flex;align-items:center;justify-content:center}
.benefit-title{font-size:14px;font-weight:700;line-height:18px;height:36px}
.benefit-text{font-size:11.5px;line-height:20px;margin-top:10px;padding:0 30px}

/* offer */
.section-title{width:1200px;text-align:center;font-size:29px;font-weight:500;color:#333;text-transform:uppercase}
.offer-card{top:1145px;width:238px}
.offer-photo{width:238px;height:240px}
.offer-label{text-align:center;font-size:16px;font-weight:500;margin-top:21px;text-transform:uppercase}
.offer-hover{background:var(--teal);color:#fff;text-align:center;padding:40px 22px 0}
.offer-hover h3{font-size:13px;font-weight:500;margin-bottom:12px}
.offer-hover p{font-size:11px;line-height:21px}
.offer-line{left:610px;top:1432px;width:238px;height:4px;background:var(--pink)}
.dot{top:1493px;height:3px}

/* faq */
.faq{left:0;top:1580px;width:1200px;height:410px;background:var(--light)}
.faq-photo{left:0;top:0;width:590px;height:410px;background:radial-gradient(ellipse at 45% 45%,#e9d6c8 0%,#dcc8bb 35%,#cfc3bc 70%,#c7c0bb 100%)}
.faq-q{left:620px;width:480px;height:52px;background:var(--pink);color:#fff;font-size:12px;font-weight:500;display:flex;align-items:center;justify-content:space-between;padding:0 16px 0 18px;text-transform:uppercase}
.faq-q span.sign{font-size:20px;font-weight:400}
.faq-a{left:638px;top:1732px;width:440px;font-size:12px;line-height:22px;color:var(--muted)}

/* testimonials */
.avatar{border-radius:50%;background:radial-gradient(circle at 50% 45%,#d7c4b8 0%,#b99f92 55%,#7d6a62 100%)}
.avatar-main{border:5px solid #fff;box-shadow:0 0 0 1px #ddd}
.quote-name{top:2358px;width:1200px;text-align:center;font-size:15px;font-weight:500}
.quote-city{top:2380px;width:1200px;text-align:center;font-size:12px;color:var(--muted)}
.quote-text{left:330px;top:2406px;width:540px;text-align:center;font-size:12px;line-height:23px;color:var(--muted)}
.stars{top:2484px;width:1200px;text-align:center;color:#c6891b;font-size:13px;letter-spacing:1px}

/* footer */
.footer-wave{left:0;top:2550px}
.footer{left:0;top:2640px;width:1200px;height:265px;background:var(--light)}
.contact{left:100px;top:2680px;font-size:12px;line-height:26px;color:#444}
.social{top:2770px;width:38px;height:38px;border-radius:50%}
.foot-col h4{font-size:18px;font-weight:500;color:#333;text-transform:uppercase;margin-bottom:22px}
.foot-col li{list-style:none;font-size:12px;color:#444;line-height:24px;padding-left:26px;position:relative}
.foot-col li::before{content:"›";position:absolute;left:0;top:-1px;color:var(--pink);font-size:16px}
.news-text{font-size:12px;line-height:22px;color:#444}
.news-input{left:806px;top:2795px;width:300px;height:34px;border:1px solid #bbb;background:#fff;font-size:11px;color:#777;padding:0 12px;display:flex;align-items:center}
.news-btn{left:806px;top:2843px;width:300px;height:34px;background:var(--teal);color:#fff;font-size:12px;font-weight:700;display:flex;align-items:center;justify-content:center;text-transform:uppercase}
.copyright{top:2932px;width:1200px;text-align:center;font-size:11px;color:#555}
</style>
</head>
<body>

<header class="site-header abs">
  <div class="brand abs"><span class="brand-mark"></span><span class="brand-name">Bright Pram Hub</span></div>
  <div class="top-phone abs">
    <svg width="14" height="14" viewBox="0 0 24 24"><path fill="#33bdb5" d="M6.6 10.8a15.1 15.1 0 0 0 6.6 6.6l2.2-2.2c.3-.3.7-.4 1-.2 1.1.4 2.3.6 3.6.6.6 0 1 .4 1 1V20c0 .6-.4 1-1 1A17 17 0 0 1 3 4c0-.6.4-1 1-1h3.5c.6 0 1 .4 1 1 0 1.3.2 2.5.6 3.6.1.3 0 .7-.2 1z"/></svg>
    1.555.014.2290
  </div>
  <a class="btn-login abs">
    <svg width="10" height="12" viewBox="0 0 10 12"><rect x="0" y="5" width="10" height="7" rx="1" fill="#fff"/><path d="M2.5 5V3.5a2.5 2.5 0 0 1 5 0V5" stroke="#fff" stroke-width="1.4" fill="none"/></svg>
    LOGIN
  </a>
  <nav class="main-nav abs">
    <a>Home</a><a>About Us</a><a>Services</a><a>What We Offer</a><a>Child Care</a><a>Senior Care</a><a>Contact Us</a>
  </nav>
</header>

<section class="hero abs">
  <div class="hero-bg abs"></div>
  <div class="hero-photo abs" role="img" aria-label="Smiling caregiver embracing an elderly woman"></div>
  <svg class="hero-wave abs" width="1200" height="140" viewBox="0 0 1200 140"><path d="M0 60 C250 150 520 130 760 90 C950 58 1100 30 1200 55 L1200 140 L0 140 Z" fill="#33bdb5"/></svg>
  <h1 class="hero-title abs">Nanny for families<br>and caregivers.</h1>
  <p class="hero-sub abs">Magni dolores eos qui ratione voluptatem</p>
  <a class="btn btn-find abs">Find Care</a>
  <a class="btn btn-search abs">Search for Nannies</a>

  <div class="benefit abs" style="left:120px">
    <div class="benefit-icon"><span style="font-size:34px;font-weight:700;color:#222">$</span></div>
    <div class="benefit-title">Reduced<br>Cost</div>
    <div class="benefit-text">Reprehenderit qui in ea voluptate velit esse quam</div>
  </div>
  <div class="benefit abs" style="left:360px">
    <div class="benefit-icon"><svg width="34" height="32" viewBox="0 0 34 32"><rect x="2" y="5" width="30" height="25" rx="2" fill="none" stroke="#222" stroke-width="2.5"/><rect x="2" y="5" width="30" height="6" fill="#222"/><g fill="#222"><rect x="7" y="15" width="4" height="3"/><rect x="15" y="15" width="4" height="3"/><rect x="23" y="15" width="4" height="3"/><rect x="7" y="22" width="4" height="3"/><rect x="15" y="22" width="4" height="3"/><rect x="23" y="22" width="4" height="3"/></g><rect x="9" y="1" width="3" height="7" fill="#222"/><rect x="22" y="1" width="3" height="7" fill="#222"/></svg></div>
    <div class="benefit-title">Increased<br>flexibility for parents</div>
    <div class="benefit-text">Reprehenderit qui in ea voluptate velit esse quam</div>
  </div>
  <div class="benefit abs" style="left:600px">
    <div class="benefit-icon"><svg width="32" height="32" viewBox="0 0 32 32"><g fill="#222"><rect x="3" y="6" width="6" height="24"/><rect x="12" y="12" width="6" height="18"/><rect x="21" y="20" width="6" height="10"/></g><path d="M6 4 L26 18" stroke="#222" stroke-width="2.5"/><path d="M21 18 H27 V12" stroke="#222" stroke-width="2.5" fill="none"/></svg></div>
    <div class="benefit-title">Reduced<br>Illness</div>
    <div class="benefit-text">Reprehenderit qui in ea voluptate velit esse quam</div>
  </div>
  <div class="benefit abs" style="left:840px">
    <div class="benefit-icon"><svg width="36" height="32" viewBox="0 0 36 32"><path d="M2 15 L18 2 L34 15" stroke="#222" stroke-width="3" fill="none"/><rect x="7" y="14" width="22" height="16" fill="#222"/><circle cx="13" cy="21" r="3" fill="#fff"/><circle cx="23" cy="21" r="3" fill="#fff"/></svg></div>
    <div class="benefit-title">Increased Socialization with other children vs. sole nanny</div>
    <div class="benefit-text">Reprehenderit qui in ea voluptate velit esse quam</div>
  </div>
</section>

<h2 class="section-title abs" style="top:1052px">What We Offer</h2>

<div class="offer-card abs" style="left:100px">
  <div class="offer-photo" role="img" aria-label="Mother hugging her smiling daughter" style="background:linear-gradient(135deg,#7a5a44,#b4866a 50%,#4f8d55)"></div>
  <div class="offer-label">Child Care</div>
</div>
<div class="offer-card abs" style="left:355px">
  <div class="offer-photo" role="img" aria-label="Home carer serving a meal to an elderly man" style="background:linear-gradient(135deg,#8a5a3c,#c9a88f 50%,#d06a3a)"></div>
  <div class="offer-label">Home Care</div>
</div>
<div class="offer-card abs" style="left:610px">
  <div class="offer-photo offer-hover">
    <h3>SENIOR CARE</h3>
    <p>Sed ut perspiciatis unde omnis iste natus error voluptatem accusantium doloremque laudantium, totam rem aperiam, eaque ipsa quae ab illo inventore veritatis et quasi</p>
  </div>
  <div class="offer-label">Learn More</div>
</div>
<div class="offer-card abs" style="left:865px">
  <div class="offer-photo" role="img" aria-label="Young woman cuddling her pet dog" style="background:linear-gradient(135deg,#5b4a40,#a88a78 50%,#d9d2cc)"></div>
  <div class="offer-label">Pet Care</div>
</div>
<div class="offer-line abs"></div>
<div class="dot abs" style="left:535px;width:58px;background:var(--teal)"></div>
<div class="dot abs" style="left:612px;width:58px;background:#ccc"></div>

<section class="faq abs">
  <div class="faq-photo abs" role="img" aria-label="Young woman embracing a smiling grandmother"></div>
</section>
<div class="faq-q abs" style="top:1663px">Q : Magni dolores eos qui ratione voluptatem sequi nesciunt<span class="sign">−</span></div>
<p class="faq-a abs">A : Duis aute irure dolor in reprehenderit in voluptate velit esse cillum dolore eu fugiat nulla pariatur. Excepteur sint occaecat cupidatat non proident</p>
<div class="faq-q abs" style="top:1793px">Q : Lorem ipsum dolor sit amet, consectetur adipiscing elit<span class="sign">+</span></div>
<div class="faq-q abs" style="top:1862px">Q : Ut enim ad minima veniam, quis nostrum exercitationem<span class="sign">+</span></div>

<h2 class="section-title abs" style="top:2078px">Our Testimonials</h2>
<div class="avatar abs" role="img" aria-label="Client portrait" style="left:104px;top:2212px;width:80px;height:80px"></div>
<div class="avatar abs" role="img" aria-label="Client portrait" style="left:228px;top:2205px;width:94px;height:94px"></div>
<div class="avatar abs" role="img" aria-label="Client portrait" style="left:370px;top:2198px;width:106px;height:106px"></div>
<div class="avatar avatar-main abs" role="img" aria-label="Featured client portrait" style="left:517px;top:2162px;width:176px;height:176px"></div>
<div class="avatar abs" role="img" aria-label="Client portrait" style="left:733px;top:2198px;width:106px;height:106px"></div>
<div class="avatar abs" role="img" aria-label="Client portrait" style="left:882px;top:2205px;width:94px;height:94px"></div>
<div class="avatar abs" role="img" aria-label="Client portrait" style="left:1020px;top:2212px;width:80px;height:80px"></div>
<div class="quote-name abs">- BY AUTHOR NAME</div>
<div class="quote-city abs">- City Location</div>
<p class="quote-text abs">Integer eget aliquet elit. Duis pretium purus vitae orci interdum, laoreet scelerisque turpis volutpat. Sed nisl velit, dignissim in pellentesque ac, accumsan in quam. Morbi quis accumsan turpis. Mauris pellentesque non elit in efficitur. Donec egestas lacinia lorem sit amet</p>
<div class="stars abs">★★★★★</div>

<svg class="footer-wave abs" width="1200" height="95" viewBox="0 0 1200 95"><path d="M0 70 C220 40 380 55 560 60 C800 66 1000 10 1200 22 L1200 95 L0 95 Z" fill="#e6e6e6"/></svg>
<footer class="footer abs"></footer>
<div class="contact abs">#45 Street Name, Eastern building, 1st Floor,USA.<br>Call us: 1-555-018-3344<br>Email: support@brightpramhub.net</div>
<span class="social abs" style="left:100px;background:#3b5b9a"></span>
<span class="social abs" style="left:155px;background:#1da1f2"></span>
<span class="social abs" style="left:210px;background:#dd4b39"></span>
<span class="social abs" style="left:265px;background:#0e76a8"></span>
<div class="foot-col abs" style="left:421px;top:2685px"><h4>Quick Links</h4><ul><li>Home</li><li>About Us</li><li>Testimonials</li><li>What we offer</li></ul></div>
<div class="foot-col abs" style="left:617px;top:2685px"><h4>Other Links</h4><ul><li>Support</li><li>Services</li><li>Contact Us</li><li>Reviews</li></ul></div>
<div class="foot-col abs" style="left:806px;top:2685px;width:300px"><h4>Newsletter</h4><p class="news-text" style="margin-top:-10px">Lorem ipsum dolor sit amet, consectetur adipiscing elit. Curabitur volutpat tincidunt facilisis.</p></div>
<div class="news-input abs">Email Id...</div>
<a class="news-btn abs">Subscribe</a>
<div class="copyright abs">Copyright © 2018 Bright Pram Hub . All rights reserved.</div>

</body>
</html>
```